Talvique Hotels Business Card and Logo

We need a business card design for a hotel group. I saw a hotel card you designed and really liked it. We have multiple properties with different brands. Were hoping that the card would be unique and find a way to list out all our properties. Our web address is www.talviquehotels.com. I have attached some photos of card designs I like.

Industry/Entity Type

Hotel

Contact Information for Business Card

Scott CurranReneson HotelsChief Operating Officer56 Madera DriveCorte Madera, CA 94925Office 415-891-5013Cell 707-5550143

```html
<!DOCTYPE html>
<html lang="en">
<head>
<meta charset="utf-8">
<title>Talvique Hotels Business Card</title>
<link href="https://fonts.googleapis.com/css2?family=Montserrat:wght@400;600&display=swap" rel="stylesheet">
<style>
  :root {
    --bg: #c9c9c9;
    --card-white: #ffffff;
    --navy: #13335f;
    --grey-text: #4a4a4a;
    --muted: #6b6b6b;
    --accent-green: #5aa832;
    --photo-deep: #2c4d6e;
    --photo-mid: #3f6f8c;
    --photo-teal: #1f8fa6;
    --shadow: rgba(0,0,0,0.28);
  }
  * { box-sizing: border-box; margin: 0; padding: 0; }
  html, body { width: 1200px; height: 930px; overflow: hidden; }
  body {
    background: var(--bg);
    font-family: "Montserrat", sans-serif;
    position: relative;
  }
  .card {
    position: absolute;
    left: 280px;
    width: 640px;
    height: 366px;
    border-radius: 24px;
    overflow: hidden;
    box-shadow: 0 10px 24px var(--shadow);
  }
  .card--front { top: 80px; }
  .card--back { top: 484px; background: var(--card-white); }

  .front-photo {
    position: absolute; inset: 0;
    background:
      radial-gradient(ellipse at 70% 80%, var(--photo-teal) 0%, transparent 55%),
      linear-gradient(160deg, var(--photo-mid) 0%, var(--photo-deep) 60%, #35607a 100%);
  }
  .front-name {
    position: absolute; inset: 0;
    display: flex; align-items: center; justify-content: center;
    font-family: "Montserrat", sans-serif;
    font-weight: 600;
    font-size: 40px;
    color: #ffffff;
  }

  .back-name {
    position: absolute;
    left: 44px; top: 150px;
    font-family: "Montserrat", sans-serif;
    font-weight: 600;
    font-size: 27px;
    color: var(--navy);
  }
  .contact {
    position: absolute;
    left: 370px; top: 78px;
    width: 250px;
  }
  .contact__name {
    font-weight: 600;
    font-size: 18px;
    color: var(--navy);
    line-height: 1.2;
    white-space: nowrap;
  }
  .contact__title {
    font-size: 12.5px;
    color: var(--muted);
    margin-top: 2px;
  }
  .contact__address {
    font-size: 14px;
    color: var(--grey-text);
    margin-top: 20px;
    line-height: 1.4;
  }
  .contact__list {
    list-style: none;
    margin-top: 18px;
    font-size: 14px;
    color: var(--grey-text);
    line-height: 1.55;
  }
  .contact__list li { display: flex; align-items: center; gap: 8px; }
  .contact__list svg { width: 11px; height: 11px; flex: none; }
</style>
</head>
<body>

<section class="card card--front">
  <div class="front-photo" role="img" aria-label="Photo of a hotel courtyard with a swimming pool, lounge chairs and a pitched-roof building under a blue tint"></div>
  <div class="front-name">Talvique Hotels</div>
</section>

<section class="card card--back">
  <div class="back-name">Talvique Hotels</div>
  <div class="contact">
    <p class="contact__name">Brent Holloway Talvique</p>
    <p class="contact__title">Hotels Chief Operating Officer</p>
    <p class="contact__address">83 Pellwick Lane<br>Larkmont, CA 94990</p>
    <ul class="contact__list">
      <li>
        <svg viewBox="0 0 12 12" aria-hidden="true"><path d="M2.5 1 L4.5 1 L5.2 3.4 L4 4.4 C4.6 5.8 6 7.3 7.6 8 L8.6 6.8 L11 7.5 L11 9.5 C11 10.3 10.3 11 9.5 11 C5 11 1 7 1 2.5 C1 1.7 1.7 1 2.5 1 Z" fill="var(--accent-green)"/></svg>
        415-555-0186
      </li>
      <li>
        <svg viewBox="0 0 12 12" aria-hidden="true"><rect x="3" y="0.8" width="6" height="10.4" rx="1.2" fill="none" stroke="var(--accent-green)" stroke-width="1.4"/><circle cx="6" cy="9.2" r="0.7" fill="var(--accent-green)"/></svg>
        707-5550143
      </li>
      <li>
        <svg viewBox="0 0 12 12" aria-hidden="true"><rect x="1" y="2.5" width="10" height="7" rx="0.8" fill="none" stroke="var(--accent-green)" stroke-width="1.3"/><path d="M1.3 3 L6 6.6 L10.7 3" fill="none" stroke="var(--accent-green)" stroke-width="1.2"/></svg>
        info@talviquehotels.com
      </li>
      <li>
        <svg viewBox="0 0 12 12" aria-hidden="true"><circle cx="6" cy="6" r="5" fill="none" stroke="var(--accent-green)" stroke-width="1.2"/><ellipse cx="6" cy="6" rx="2.2" ry="5" fill="none" stroke="var(--accent-green)" stroke-width="1"/><path d="M1 6 H11" stroke="var(--accent-green)" stroke-width="1"/></svg>
        www.talviquehotels.com
      </li>
    </ul>
  </div>
</section>

</body>
</html>
```